Machining Business Order Thank You Insert

I am looking for a business style card to include with orders that I ship. The card needs to thank the recipient for their order, and encourage them to leave a review. The card should include my business name and contact information and have an area to hand write a message.

I mainly sale on Craftlane and my own website. We are a machining an manufacturing business that are in the sale of mostly metal machined and 3d printed plastic products.

The front of the card should include the following:
Logo: (attached)
Snapgram: https://www.snapgram.example/kelvomill/
Friendsbook: https://www.friendsbook.example/KelvoMill
Website: https://www.kelvomill.example/

The back of the card needs an area to write a message

Industry/Entity Type

3D Printing, Machining, Craftlane

Contact Information for Business Card

Black or white front, white back to write a personal message

Font styles to use
Sans Serif

Colors

Designer to choose colors to be used in the design.

Requirements
Must have
• Encourage a review, social media info

```html
<!DOCTYPE html>
<html lang="en">
<head>
<meta charset="utf-8">
<title>KelvoMill – Thank You Insert</title>
<link rel="stylesheet" href="https://fonts.googleapis.com/css2?family=Barlow:wght@400;500;600&family=Kaushan+Script&display=swap">
<style>
  :root {
    --backdrop: #8d9092;
    --card-dark: #1c1c1c;
    --card-mid: #3a3a3a;
    --card-light: #4b4b4b;
    --accent: #e8542a;
    --muted: #7d7d7d;
    --soft-text: #a8a8a8;
    --write-line: #ffffff;
  }
  html, body {
    margin: 0;
    padding: 0;
    width: 1200px;
    height: 928px;
    overflow: hidden;
    background: var(--backdrop);
  }
  .canvas {
    position: relative;
    width: 1200px;
    height: 928px;
  }
  .card {
    position: absolute;
    border-radius: 18px;
    overflow: hidden;
    background: linear-gradient(100deg, var(--card-dark) 0%, var(--card-mid) 45%, var(--card-light) 70%, var(--card-dark) 100%);
  }
  .card--front { left: 267px; top: 59px; width: 670px; height: 383px; }
  .card--back  { left: 264px; top: 484px; width: 675px; height: 386px; }

  /* front: brand block */
  .brand {
    position: absolute;
    left: 40px;
    top: 92px;
    width: 210px;
    display: flex;
    flex-direction: column;
    align-items: center;
  }
  .brand__mark {
    width: 90px;
    height: 90px;
    border: 4px solid var(--accent);
    box-sizing: border-box;
    margin-bottom: 36px;
  }
  .brand__name {
    font-family: "Barlow", sans-serif;
    font-weight: 500;
    font-size: 27px;
    letter-spacing: 7px;
    color: var(--accent);
    line-height: 1;
  }

  /* front: writing lines */
  .write-line {
    position: absolute;
    left: 287px;
    width: 339px;
    height: 48px;
    border-radius: 24px;
    background: var(--write-line);
  }
  .write-line--1 { top: 82px; }
  .write-line--2 { top: 166px; }
  .write-line--3 { top: 251px; }

  /* back: thank-you message */
  .thanks {
    position: absolute;
    font-family: "Kaushan Script", cursive;
    line-height: 1;
  }
  .thanks--thank { left: 228px; top: 104px; font-size: 70px; color: var(--accent); transform: rotate(-4deg); }
  .thanks--you   { left: 226px; top: 178px; font-size: 72px; color: var(--muted); transform: rotate(-4deg); }
  .order-line {
    position: absolute;
    font-family: "Barlow", sans-serif;
    font-weight: 500;
    line-height: 1;
    transform: rotate(-12deg);
    transform-origin: left bottom;
  }
  .order-line--for  { left: 370px; top: 204px; font-size: 32px; color: var(--accent); }
  .order-line--your { left: 253px; top: 273px; font-size: 32px; color: var(--accent); }
  .order-line--your .order-line__muted { color: var(--muted); }

  /* back: review strip */
  .review {
    position: absolute;
    left: 22px;
    right: 22px;
    top: 335px;
    display: flex;
    align-items: center;
    gap: 10px;
    font-family: "Barlow", sans-serif;
    font-size: 16px;
    color: var(--soft-text);
    letter-spacing: 0.4px;
    white-space: nowrap;
  }
  .review__label { font-weight: 600; margin-right: 4px; }
  .review__item { display: flex; align-items: center; gap: 5px; margin-right: 4px; }
  .review__dot {
    width: 15px; height: 15px;
    background: var(--accent);
    border-radius: 3px;
  }
  .review__dot--round { border-radius: 50%; }
</style>
</head>
<body>
<main class="canvas">

  <section class="card card--front" aria-label="Card front">
    <div class="brand">
      <div class="brand__mark"></div>
      <div class="brand__name">KELVOMILL</div>
    </div>
    <div class="write-line write-line--1"></div>
    <div class="write-line write-line--2"></div>
    <div class="write-line write-line--3"></div>
  </section>

  <section class="card card--back" aria-label="Card back">
    <div class="thanks thanks--thank">Thank</div>
    <div class="thanks thanks--you">You</div>
    <div class="order-line order-line--for">for</div>
    <div class="order-line order-line--your">Your <span class="order-line__muted">Order</span></div>

    <div class="review">
      <span class="review__label">Leave A Review:</span>
      <span class="review__item"><span class="review__dot"></span>@kelvomill</span>
      <span class="review__item"><span class="review__dot"></span>@KelvoMill</span>
      <span class="review__item"><span class="review__dot review__dot--round"></span>www.kelvomill.example</span>
    </div>
  </section>

</main>
</body>
</html>
```